PowerPoint Design

We require a sample PowerPoint design so we can pitch PPT design services to a client.

The designs do NOT need to be done in PowerPoint, but should reflect designs that *could* be created in PPT format.

We require 3 slides as part of this project:

1. A slide containing the statistical chart based on data in Figure 3.3 at http://www4.qorvelist.example/survey-tables/2006/tb-rv/gx-hy/index.cfm?LANG=ENG&VIEW=C&format=flash&PRCODE=01&TOPIC_ID=2
-> note, don't just copy and paste the existing graph - come up with something innovative and eye catching

2. Inspirational slide to motivate employees. Zibrant "inspirational quote" and select a quote you think is appropriate. Imagery should generate enthusiasm/optimism.

3. A slide of your own choosing.
Updates

Project Deadline Extended
Reason: One of the team reviewing the designs is away from office. We've decided to give other designers a chance to submit ideas. Final decision will be made on December 5th, 2011.

Target Market(s)

Business professionals

Industry/Entity Type

Zibrant

Requirements
Must have
• Must have 3 slides.

```html
<!DOCTYPE html>
<html lang="en">
<head>
<meta charset="utf-8">
<title>Occupied private dwellings by structural type of dwelling, Canada, 2006</title>
<link href="https://fonts.googleapis.com/css2?family=Libre+Baskerville&family=Open+Sans:ital,wght@0,400;0,700;1,400&display=swap" rel="stylesheet">
<style>
  :root {
    --bg-light: #cfcfcf;
    --bg-mid: #8c8c8c;
    --bg-dark: #4f4f4f;
    --ink: #111111;
    --panel: #ffffff;
    --grid: #c4c4c4;
    --axis-text: #8a8a8a;
    --legend-text: #8e8e8e;
    --logo-box: #a3a3a3;
    --logo-text: #6e6e6e;
    --single: #b06e06;
    --semi: #8b8b8d;
    --row: #55bfe0;
    --duplex: #8ea676;
    --low-rise: #9e283b;
    --high-rise: #d07667;
    --other: #444444;
  }
  html, body {
    margin: 0;
    width: 1200px;
    height: 900px;
    overflow: hidden;
  }
  .slide {
    position: relative;
    width: 1200px;
    height: 900px;
    background: radial-gradient(ellipse 1300px 1100px at 0% 0%, var(--bg-light) 0%, var(--bg-mid) 55%, var(--bg-dark) 100%);
    font-family: "Open Sans", Arial, sans-serif;
  }
  .slide-title {
    position: absolute;
    top: 44px;
    left: 0;
    width: 1156px;
    margin: 0;
    text-align: center;
    font-family: "Libre Baskerville", Georgia, serif;
    font-weight: 400;
    font-size: 35px;
    line-height: 56px;
    color: var(--ink);
  }
  .logo-placeholder {
    position: absolute;
    left: 1049px;
    top: 30px;
    width: 120px;
    height: 86px;
    background: var(--logo-box);
    display: flex;
    align-items: center;
    justify-content: center;
    text-align: center;
    font-weight: 700;
    font-size: 30px;
    line-height: 29px;
    color: var(--logo-text);
    letter-spacing: -1px;
  }
  .chart-panel {
    position: absolute;
    left: 116px;
    top: 193px;
    width: 984px;
    height: 632px;
    background: var(--panel);
    box-shadow: 0 14px 30px rgba(0,0,0,0.45);
  }
  .chart-panel svg { position: absolute; left: -116px; top: -193px; }
  .grid line { stroke: var(--grid); stroke-width: 1; }
  .baseline { stroke: #222; stroke-width: 1.5; }
  .tick-label { font-size: 12px; font-weight: 700; fill: var(--axis-text); text-anchor: end; }
  .axis-title { font-size: 14px; font-style: italic; fill: var(--axis-text); text-anchor: middle; }
  .bar-value { font-size: 14px; font-weight: 700; fill: var(--ink); text-anchor: middle; }
  .legend-box { fill: var(--panel); filter: drop-shadow(0 2px 4px rgba(0,0,0,0.3)); }
  .legend-label { font-size: 16px; font-style: italic; fill: var(--legend-text); }
</style>
</head>
<body>
<div class="slide">
  <h1 class="slide-title">Occupied private dwellings<br>by structural type of dwelling, Canada, 2006</h1>
  <div class="logo-placeholder">YOUR<br>LOGO</div>

  <div class="chart-panel">
    <svg width="1200" height="900" viewBox="0 0 1200 900" role="img" aria-label="Bar chart of occupied private dwellings by structural type, Canada, 2006">
      <g class="grid">
        <line x1="283" y1="267" x2="860" y2="267"/>
        <line x1="283" y1="351" x2="860" y2="351"/>
        <line x1="283" y1="435" x2="860" y2="435"/>
        <line x1="283" y1="518" x2="860" y2="518"/>
        <line x1="283" y1="602" x2="860" y2="602"/>
        <line x1="283" y1="686" x2="860" y2="686"/>
      </g>
      <g>
        <text class="tick-label" x="265" y="272">60 %</text>
        <text class="tick-label" x="265" y="356">50 %</text>
        <text class="tick-label" x="265" y="440">40 %</text>
        <text class="tick-label" x="265" y="523">30 %</text>
        <text class="tick-label" x="265" y="607">20 %</text>
        <text class="tick-label" x="265" y="691">10 %</text>
        <text class="tick-label" x="265" y="775">0 %</text>
      </g>
      <text class="axis-title" transform="translate(185 518) rotate(-90)">% of total occupied private dwellings</text>

      <g class="bars">
        <rect x="311" y="306" width="60" height="464" fill="var(--single)"/>
        <rect x="388" y="730" width="60" height="40" fill="var(--semi)"/>
        <rect x="464" y="723" width="60" height="47" fill="var(--row)"/>
        <rect x="541" y="726" width="60" height="44" fill="var(--duplex)"/>
        <rect x="618" y="616" width="60" height="154" fill="var(--low-rise)"/>
        <rect x="695" y="695" width="60" height="75" fill="var(--high-rise)"/>
        <rect x="772" y="757" width="59" height="13" fill="var(--other)"/>
      </g>
      <g>
        <text class="bar-value" x="341" y="297">55,3 %</text>
        <text class="bar-value" x="418" y="721">4,8 %</text>
        <text class="bar-value" x="494" y="713">5,6 %</text>
        <text class="bar-value" x="571" y="716">5,3 %</text>
        <text class="bar-value" x="648" y="606">18,4 %</text>
        <text class="bar-value" x="725" y="685">8,9 %</text>
        <text class="bar-value" x="801" y="747">1,6 %</text>
      </g>
      <line class="baseline" x1="283" y1="770" x2="860" y2="770"/>

      <rect class="legend-box" x="487" y="323" width="513" height="222"/>
      <g>
        <rect x="517" y="352" width="16" height="16" fill="var(--single)"/>
        <text class="legend-label" x="548" y="366">Single-detached houses</text>
        <rect x="517" y="377" width="16" height="16" fill="var(--semi)"/>
        <text class="legend-label" x="548" y="391">Semi-detached houses</text>
        <rect x="517" y="401" width="16" height="16" fill="var(--row)"/>
        <text class="legend-label" x="548" y="415">Row houses</text>
        <rect x="517" y="426" width="16" height="16" fill="var(--duplex)"/>
        <text class="legend-label" x="548" y="440">Apartments, duplex</text>
        <rect x="517" y="450" width="16" height="16" fill="var(--low-rise)"/>
        <text class="legend-label" x="548" y="464">Apartments in buildings with fewer than five storeys</text>
        <rect x="517" y="475" width="16" height="16" fill="var(--high-rise)"/>
        <text class="legend-label" x="548" y="489">Apartments in buildings with five or more storeys</text>
        <rect x="517" y="499" width="16" height="16" fill="var(--other)"/>
        <text class="legend-label" x="548" y="513">Other dwellings</text>
      </g>
    </svg>
  </div>
</div>
</body>
</html>
```